Satchel & Sundial needs new business card design

I need a new business card design. I'm looking for out-of-the-box design which represents the freedom of being a location independent entrepreneur.
I offer coaching, retreats and trips.
I would like to see designs with and without the photo.
Colors I use are black (#000000), green (#25A796) and brown (#D7C38C)
Website satchelandsundial.example

Target Market(s)

location independent entrepreneurs, digital nomads, people looking to swap the 9 to 5 for a lifestyle business

Industry/Entity Type

Business

Contact Information for Business Card

Dorota Falkner
Your Lifestyle Business Coach, Retreat & Trip Leader
http://satchelandsundial.example
hello@satchelandsundial.example
Live a life you don't need a holiday from

Font styles to use
Serif
Sans Serif

Requirements
Must have
• One side should contain only the logo. I would also consider having the "Live a life you don't need a holiday from" on that side too (depending on how it looks)
• Please show both sides on the designs.

```html
<!DOCTYPE html>
<html lang="en">
<head>
<meta charset="utf-8">
<title>Satchel &amp; Sundial — Business Card</title>
<link rel="stylesheet" href="https://fonts.googleapis.com/css2?family=Open+Sans:wght@400;600;700&display=swap">
<style>
  :root {
    --teal: #25A796;
    --ink: #1c1a1a;
    --white: #ffffff;
    --stage: #e6e6e6;
    --muted: #555555;
  }
  * { margin: 0; padding: 0; box-sizing: border-box; }
  html, body {
    width: 1105px;
    height: 1200px;
    overflow: hidden;
    background: var(--stage);
    font-family: "Open Sans", sans-serif;
  }
  .canvas {
    position: relative;
    width: 1105px;
    height: 1200px;
  }
  .card {
    position: absolute;
    left: 192px;
    width: 721px;
    height: 412px;
    overflow: hidden;
  }
  .card--front { top: 146px; background: var(--white); }
  .card--back  { top: 602px; background: var(--teal); }

  .brand-name {
    position: absolute;
    left: 0;
    width: 100%;
    text-align: center;
    font-weight: 700;
    font-size: 44px;
    letter-spacing: 1px;
    text-transform: uppercase;
    line-height: 1;
  }
  .card--front .brand-name { top: 82px; color: var(--ink); }
  .card--back .brand-name  { top: 180px; color: var(--white); }

  .contact {
    position: absolute;
    left: 0;
    top: 232px;
    width: 100%;
    text-align: center;
  }
  .contact__name {
    color: var(--teal);
    font-weight: 600;
    font-size: 22px;
    letter-spacing: 0.5px;
    text-transform: uppercase;
    line-height: 30px;
  }
  .contact__role {
    color: var(--ink);
    font-size: 18.5px;
    line-height: 30px;
  }
  .contact__email {
    color: var(--muted);
    font-size: 17.5px;
    line-height: 30px;
  }
  .contact__email-label { color: var(--teal); font-weight: 600; }

  .footer-bands {
    position: absolute;
    left: 0;
    bottom: 0;
    width: 721px;
    height: 50px;
  }
  .website {
    position: absolute;
    right: 26px;
    bottom: 12px;
    color: var(--white);
    font-size: 17.5px;
  }

  .social {
    position: absolute;
    top: 26px;
    right: 24px;
    display: flex;
    gap: 4px;
  }
  .social__tile {
    width: 23px;
    height: 23px;
    background: var(--white);
  }
  .tagline {
    position: absolute;
    left: 0;
    top: 342px;
    width: 100%;
    text-align: center;
    color: var(--white);
    font-size: 17px;
    text-transform: uppercase;
    letter-spacing: 0.2px;
  }
</style>
</head>
<body>
<main class="canvas">

  <section class="card card--front" aria-label="Card front">
    <p class="brand-name">Satchel &amp; Sundial</p>

    <div class="contact">
      <p class="contact__name">Dorota Falkner</p>
      <p class="contact__role">Your Lifestyle Business Coach, Retreat &amp; Trip Leader</p>
      <p class="contact__email"><span class="contact__email-label">Email:</span> hello@satchelandsundial.example</p>
    </div>

    <svg class="footer-bands" viewBox="0 0 721 50" aria-hidden="true">
      <polygon points="0,20 388,20 384,29 0,29" fill="var(--teal)"/>
      <polygon points="0,34 721,34 721,50 0,50" fill="var(--ink)"/>
      <polygon points="412,0 721,0 721,50 390,50" fill="var(--ink)"/>
    </svg>
    <p class="website">www.satchelandsundial.example</p>
  </section>

  <section class="card card--back" aria-label="Card back">
    <div class="social" aria-label="Social links">
      <span class="social__tile"></span>
      <span class="social__tile"></span>
      <span class="social__tile"></span>
    </div>
    <p class="brand-name">Satchel &amp; Sundial</p>
    <p class="tagline">Live a life you don’t need a holiday from</p>
  </section>

</main>
</body>
</html>
```